Looking for a cool & simple business-card-design for digital agency

Hi!

We are a web agency that offers Reputation Management, Vextor & Seo Services and software development. We like cool things, we like innovative styles.

We have uploaded our logo.

Project Deadline Extended Reason: Client does not want any designs with the colorful logo. Please send us submissions ONLY with the blac and white logo. What the client would like to see:1) Back of the card: is a silver logo on a black background2) front of the card with all the data, please use white background and black logo thank you Added Friday, May 8, 2015

Industry/Entity Type

Software

```html
<!DOCTYPE html>
<html lang="de">
<head>
<meta charset="utf-8">
<title>NetPrime AG – Visitenkarte</title>
<link rel="stylesheet" href="https://fonts.googleapis.com/css2?family=Lato:wght@400;700;900&display=swap">
<style>
  :root {
    --backdrop: #3a2f26;
    --card-black: #050505;
    --card-white: #ffffff;
    --ink: #111111;
    --silver: #d6d6d6;
    --silver-dim: #9a9a9a;
    --pill: #b3b3b3;
  }
  * { box-sizing: border-box; margin: 0; padding: 0; }
  html, body {
    width: 1200px; height: 905px; overflow: hidden;
    background: var(--backdrop);
    font-family: "Lato", sans-serif;
  }
  .stage {
    position: relative; width: 1200px; height: 905px;
    display: flex; flex-direction: column; align-items: center; justify-content: center; gap: 44px;
  }
  .card {
    position: relative; width: 660px; height: 378px;
    box-shadow: 0 14px 30px rgba(0,0,0,.45);
    overflow: hidden;
  }

  /* Back side */
  .card--back { background: var(--card-black); color: var(--silver); }
  .card--back .brand {
    position: absolute; left: 200px; top: 118px;
  }
  .brand__mark {
    display: inline-block; width: 22px; height: 22px; margin-right: 12px; vertical-align: middle;
  }
  .card--back .brand__mark { background: var(--silver); }
  .brand__name {
    font-weight: 900; font-size: 38px; letter-spacing: 1px; vertical-align: middle;
  }
  .brand__tagline {
    display: block; font-weight: 400; font-size: 14px; letter-spacing: 8px;
    text-transform: uppercase; margin-top: 4px; padding-left: 34px;
  }
  .card--back .brand__tagline { color: var(--silver-dim); }
  .services {
    position: absolute; left: 234px; top: 212px; width: 380px;
    font-size: 16px; line-height: 1.4; color: #e6e6e6;
  }

  /* Front side */
  .card--front { background: var(--card-white); color: var(--ink); }
  .card--front .brand {
    position: absolute; left: 110px; top: 56px;
  }
  .card--front .brand__mark { background: var(--ink); }
  .card--front .brand__tagline { color: #333; }
  .role-pill {
    position: absolute; left: 150px; top: 162px; width: 360px; height: 54px;
    background: var(--pill); border-radius: 27px;
    display: flex; align-items: center; justify-content: center; gap: 18px;
    font-size: 19px;
  }
  .role-pill__name { font-weight: 900; }
  .role-pill__divider { width: 2px; height: 30px; background: var(--ink); }
  .role-pill__title { font-weight: 400; }
  .contact {
    position: absolute; left: 0; right: 0; top: 256px;
    display: flex; justify-content: center; gap: 22px;
    font-size: 17px;
  }
  .contact__item { display: flex; align-items: center; gap: 6px; }
  .contact__item svg { width: 16px; height: 16px; fill: var(--ink); }
  .card--front .band {
    position: absolute; left: 0; right: 0; bottom: 0; height: 64px; background: var(--card-black);
  }
</style>
</head>
<body>
<main class="stage">
  <section class="card card--back" aria-label="Kartenrückseite">
    <div class="brand">
      <span class="brand__mark"></span><span class="brand__name">NetPrime AG</span>
      <span class="brand__tagline">Digitale Strategien</span>
    </div>
    <p class="services">Reputation Management, Vextor &amp; Seo Services and Software development.</p>
  </section>

  <section class="card card--front" aria-label="Kartenvorderseite">
    <div class="brand">
      <span class="brand__mark"></span><span class="brand__name">NetPrime AG</span>
      <span class="brand__tagline">Digitale Strategien</span>
    </div>
    <div class="role-pill">
      <span class="role-pill__name">Lukas Brenner</span>
      <span class="role-pill__divider"></span>
      <span class="role-pill__title">Director</span>
    </div>
    <div class="contact">
      <span class="contact__item">
        <svg viewBox="0 0 16 16" aria-hidden="true"><path d="M2 5c0-2 2-3 6-3s6 1 6 3v1h-3V5H5v1H2z"/><path d="M4 7h8l2 6H2z"/></svg>
        000 222 3334
      </span>
      <span class="contact__item">
        <svg viewBox="0 0 16 16" aria-hidden="true"><path d="M1 3h14v10H1z M2 4l6 5 6-5" stroke="#fff" stroke-width="1"/></svg>
        info@netprimeag.com
      </span>
      <span class="contact__item">
        <svg viewBox="0 0 16 16" aria-hidden="true"><circle cx="8" cy="8" r="7"/><path d="M1 8h14M8 1v14M3 4h10M3 12h10" stroke="#fff" stroke-width="1" fill="none"/><ellipse cx="8" cy="8" rx="3.5" ry="7" stroke="#fff" stroke-width="1" fill="none"/></svg>
        www.netprimeag.com
      </span>
    </div>
    <div class="band"></div>
  </section>
</main>
</body>
</html>
```